Telecommunications/Power civil contractor needs business card design

Were a new telecommunications/power underground civil contractor that is looking for a new business card design. Our company colours are silver or grey and orange. Feel free to use the white background logo or the black background logo.

Target Market(s)

Local contractors, utility companies, private sector mining/energy companies, developers.

Industry/Entity Type

Telecommunications

Contact Information for Business Card

Each card will need the following info:
Persons name:
Title:
E-mail:
Phone number:
Shop Address:
Mailing Address:

Requirements
Must have
• Each card will need the following info:
• Persons name:
• Title:
• E-mail:
• Phone number:
• Shop Address:
• Mailing Address:

```html
<!DOCTYPE html>
<html lang="en">
<head>
<meta charset="utf-8">
<title>Ridgeline Conduit Works – Business Card</title>
<link href="https://fonts.googleapis.com/css2?family=Raleway:wght@400;500;700;800&display=swap" rel="stylesheet">
<style>
  :root {
    --backdrop: #e9e7e3;
    --paper: #f7f7f6;
    --paper-shade: #e6e6e5;
    --band-light: #8a8a8a;
    --band-dark: #4a4a4a;
    --accent: #ec5b24;
    --ink-grey: #6b6b6b;
    --ink-light: #f4f4f4;
    --ink-soft: #d9d9d9;
  }
  * { box-sizing: border-box; margin: 0; padding: 0; }
  html, body {
    width: 1200px; height: 1022px; overflow: hidden;
    background: var(--backdrop);
    font-family: "Raleway", sans-serif;
  }
  .canvas {
    width: 1200px; height: 1022px;
    display: flex; align-items: center; justify-content: center;
  }
  .card {
    position: relative;
    width: 1000px; height: 572px;
    border-radius: 26px;
    overflow: hidden;
    background: linear-gradient(180deg, var(--paper) 0%, var(--paper-shade) 100%);
    box-shadow: 0 14px 40px rgba(0,0,0,.22);
  }
  .brand {
    position: absolute; top: 0; left: 0; right: 0; height: 262px;
    display: flex; align-items: center; justify-content: center; gap: 22px;
  }
  .brand-dot {
    width: 74px; height: 74px; border-radius: 50%;
    background: var(--accent);
  }
  .brand-name {
    color: var(--ink-grey);
    font-weight: 800;
    font-size: 40px;
    line-height: 1.1;
    letter-spacing: 1px;
    text-transform: uppercase;
  }
  .accent-line {
    position: absolute; left: 0; right: 0; top: 262px; height: 5px;
    background: var(--accent);
  }
  .info-band {
    position: absolute; left: 0; right: 0; top: 275px; bottom: 0;
    background: linear-gradient(180deg, var(--band-light) 0%, var(--band-dark) 100%);
    display: flex; align-items: center;
    padding: 0 60px;
    color: var(--ink-light);
  }
  .person { flex: 0 0 400px; }
  .person-name {
    font-size: 40px; font-weight: 700; letter-spacing: 1px;
    text-transform: uppercase;
  }
  .person-title {
    color: var(--accent); font-size: 24px; font-weight: 500;
    text-align: right; width: 300px; margin: 2px 0 18px;
  }
  .shop-address { font-size: 24px; line-height: 1.4; color: var(--ink-soft); }
  .divider {
    width: 2px; height: 180px; margin: 0 46px;
    background: linear-gradient(180deg, transparent, rgba(255,255,255,.75), transparent);
  }
  .contact { font-size: 22px; line-height: 1.45; color: var(--ink-soft); }
  .mailing { text-transform: uppercase; margin-bottom: 6px; }
  .contact-row { display: flex; align-items: center; gap: 12px; }
  .contact-row svg { width: 18px; height: 18px; flex: 0 0 18px; }
</style>
</head>
<body>
<main class="canvas">
  <article class="card">
    <header class="brand">
      <span class="brand-dot"></span>
      <span class="brand-name">Ridgeline Conduit<br>Works Inc</span>
    </header>
    <div class="accent-line"></div>
    <section class="info-band">
      <div class="person">
        <h1 class="person-name">Marla Quinn</h1>
        <p class="person-title">Director</p>
        <p class="shop-address">48 Quarry Lane<br>Harlow Falls, NY 12690</p>
      </div>
      <div class="divider"></div>
      <div class="contact">
        <p class="mailing">PO Box 3158<br>Elm Hollow, CA 91780</p>
        <p class="contact-row">
          <svg viewBox="0 0 18 18"><rect x="4" y="1" width="10" height="16" rx="2" fill="none" stroke="var(--accent)" stroke-width="2"/></svg>
          +330 5180-2294
        </p>
        <p class="contact-row">
          <svg viewBox="0 0 18 18"><path d="M4 2 L7 2 L8 6 L6 7.5 Q8 11 10.5 12 L12 10 L16 11 L16 14 Q15 16 12 16 Q3 13 2 4 Q2 2 4 2 Z" fill="var(--accent)"/></svg>
          +330 6723-4018
        </p>
        <p class="contact-row">
          <svg viewBox="0 0 18 18"><rect x="1.5" y="3.5" width="15" height="11" fill="none" stroke="var(--accent)" stroke-width="2"/><path d="M2 4 L9 10 L16 4" fill="none" stroke="var(--accent)" stroke-width="2"/></svg>
          info@ridgelineconduit.com
        </p>
        <p class="contact-row">
          <svg viewBox="0 0 18 18"><circle cx="9" cy="9" r="7.5" fill="none" stroke="var(--accent)" stroke-width="2"/><path d="M1.5 9 H16.5 M9 1.5 Q4 9 9 16.5 M9 1.5 Q14 9 9 16.5" fill="none" stroke="var(--accent)" stroke-width="1.5"/></svg>
          www.ridgelineconduit.com
        </p>
      </div>
    </section>
  </article>
</main>
</body>
</html>
```